Talvique Hotels Business Card and Logo

We need a business card design for a hotel group. I saw a hotel card you designed and really liked it. We have multiple properties with different brands. Were hoping that the card would be unique and find a way to list out all our properties. Our web address is www.talviquehotels.com. I have attached some photos of card designs I like.

Industry/Entity Type

Hotel

Contact Information for Business Card

Scott CurranReneson HotelsChief Operating Officer56 Madera DriveCorte Madera, CA 94925Office 415-891-5013Cell 707-5550143

```html
<!DOCTYPE html>
<html lang="en">
<head>
<meta charset="utf-8">
<title>Talvique Hotels Business Card</title>
<link rel="stylesheet" href="https://fonts.googleapis.com/css2?family=Montserrat:wght@400;500&display=swap">
<style>
  :root {
    --stage: #1b1b1d;
    --teal: #416a7c;
    --teal-ink: #3d6274;
    --gold: #dc9127;
    --paper: #ffffff;
    --white: #ffffff;
  }
  * { margin: 0; padding: 0; box-sizing: border-box; }
  html, body {
    width: 1200px;
    height: 1189px;
    overflow: hidden;
    background: var(--stage);
    font-family: "Montserrat", Arial, sans-serif;
  }
  .canvas {
    position: relative;
    width: 1200px;
    height: 1189px;
  }
  .card {
    position: absolute;
    left: 130px;
    width: 940px;
    height: 537px;
    display: flex;
    flex-direction: column;
    align-items: center;
  }
  .card-back {
    top: 38px;
    background: var(--teal);
    justify-content: center;
  }
  .card-front {
    top: 614px;
    background: var(--paper);
    padding-top: 70px;
    overflow: hidden;
  }
  .brand {
    display: flex;
    flex-direction: column;
    align-items: center;
    gap: 26px;
  }
  .brand-dot {
    width: 96px;
    height: 96px;
    border-radius: 50%;
  }
  .brand-name {
    font-weight: 400;
    font-size: 40px;
    letter-spacing: 3px;
    text-transform: uppercase;
    line-height: 1;
  }
  .card-back .brand-dot { background: var(--white); }
  .card-back .brand-name { color: var(--white); }
  .card-front .brand-dot { background: var(--teal-ink); }
  .card-front .brand-name { color: var(--teal-ink); }
  .person {
    margin-top: 34px;
    text-align: center;
  }
  .person-name {
    color: var(--teal-ink);
    font-weight: 500;
    font-size: 29px;
    letter-spacing: 1.5px;
    text-transform: uppercase;
    line-height: 1.1;
  }
  .person-title {
    color: var(--gold);
    font-size: 22px;
    letter-spacing: 0.5px;
    margin-top: 2px;
  }
  .contact {
    margin-top: 34px;
    text-align: center;
    color: var(--teal-ink);
    font-size: 22px;
    letter-spacing: 0.5px;
    line-height: 1.6;
  }
  .contact .label { color: var(--gold); }
  .contact .sep { margin: 0 8px; }
  .contact .web-name { color: var(--gold); }
  .front-band {
    position: absolute;
    left: 0;
    bottom: 0;
    width: 100%;
    height: 16px;
    background: var(--gold);
  }
</style>
</head>
<body>
<main class="canvas">
  <section class="card card-back" aria-label="Business card back">
    <div class="brand">
      <span class="brand-dot"></span>
      <span class="brand-name">Talvique Hotels</span>
    </div>
  </section>

  <section class="card card-front" aria-label="Business card front">
    <div class="brand">
      <span class="brand-dot"></span>
      <span class="brand-name">Talvique Hotels</span>
    </div>
    <div class="person">
      <p class="person-name">Brent Holloway</p>
      <p class="person-title">Chief Operating Officer</p>
    </div>
    <div class="contact">
      <p class="address">83 Pellwick Lane, Brinsell Bay, CA 94931</p>
      <p class="phones">
        <span class="label">Office:</span> 415-555-0186<span class="sep">|</span><span class="label">Cell:</span> 707-5550143<span class="sep">|</span>www.<span class="web-name">talviquehotels</span>.com
      </p>
    </div>
    <div class="front-band"></div>
  </section>
</main>
</body>
</html>
```